Simple, 1-Page Project - Life-saving AED Devices

We recently kicked off a project to bring all geographic location records for automatic emergency defibrillators (AEDs) in the State of New York online (instead of kept in paper in drawers). This hope is that is will ultimately save thousands of lives, as 9-1-1 operators will be able to quickly direct civilians to the nearest AED to bring to people suffering a cardiac event (e.g., a heart attack).

This page will be used to describe this effort, our progress thus far and how far we have left to go.

I am looking for a 1-page design - coded for both a responsive version for mobile devices and a traditional version - that would ***ideally*** plug into my existing WordPress site (https://qv-lmt.org), but it's not a requirement.

Target Market(s)

General public (non-physicians/non-EMTs)

Requirements
Must have
• - Our logo (please note, our logo is the Birchfield Vale Chapter logo...attached)
Nice to have
• - Would be wonderful to have an area with a clickable map showing where the participating regions are - which, once clicked, will take to you their specific sites. Regions are large chunks of land encompassing multiple towns, NOT a singular, specific place A nice-looking Google Map, a la Plumtail Grids (https://plumtailgrids.com/) would be cool if this were possible..
• - If you need a headline or page title, you can use: "Bringing AEDs in New York Online"
• - Would be nice if the design incorporated the color scheme of our brand (see attachment) and/or our main website: https://qv-lmt.org/
• - Would be nice to have some AED imagery - I attached some common symbols seen in AED advertising for inspiration
Should not have
• - This is a serious topic, so the design should be respectful and not too silly/cartoonish
• - Stock images, if chosen, should be thoughtful and classy

```html
<!DOCTYPE html>
<html lang="en">
<head>
<meta charset="utf-8">
<title>Bringing AEDs in New York Online</title>
<link href="https://fonts.googleapis.com/css2?family=Marcellus&family=Lato:wght@400;700&display=swap" rel="stylesheet">
<style>
:root{
  --navy:#0f2352;
  --navy-deep:#0b1a3d;
  --red:#c8202f;
  --ink:#2b2f38;
  --muted:#6f7480;
  --soft:#f0f1f4;
  --line:#d9dce2;
  --footer:#252628;
  --white:#ffffff;
}
*{box-sizing:border-box;margin:0;padding:0}
html,body{width:1200px;height:3356px;overflow:hidden}
body{font-family:"Lato",Arial,sans-serif;color:var(--ink);background:var(--white);position:relative}
.serif{font-family:"Marcellus",Georgia,serif}
section,header,footer{position:absolute;left:0;width:1200px}

/* header */
.site-header{top:0;height:112px;background:var(--white);box-shadow:0 2px 6px rgba(0,0,0,.08);z-index:2}
.brand{position:absolute;left:112px;top:28px;display:flex;align-items:center;gap:14px}
.brand-dot{width:56px;height:56px;border-radius:50%;background:var(--navy)}
.brand-name{font-family:"Marcellus",Georgia,serif;font-size:24px;color:var(--navy);line-height:1.05;width:170px}
.main-nav{position:absolute;right:60px;top:48px;display:flex;gap:46px}
.main-nav a{font-size:15px;letter-spacing:1px;color:var(--navy);text-decoration:none}

/* hero */
.hero{top:112px;height:668px;background:linear-gradient(120deg,#c9c3c4 0%,#9c8f93 35%,#d8d2d0 60%,#7a6f73 100%)}
.hero-panel{position:absolute;left:352px;top:208px;width:536px;height:288px;background:rgba(20,20,24,.62);text-align:center;color:var(--white);padding-top:44px}
.hero-panel h1{font-family:"Marcellus",Georgia,serif;font-weight:400;line-height:1.15}
.hero-panel .l1{font-size:30px;letter-spacing:2px;display:block}
.hero-panel .l2{font-size:40px;letter-spacing:2px;display:block}
.hero-panel p{font-size:15px;line-height:1.5;margin:16px 50px 24px;color:#e6e6ea}
.btn{display:inline-block;background:var(--navy);color:var(--white);font-size:14px;letter-spacing:1px;padding:14px 34px;border-radius:30px;text-decoration:none}
.hero-dots{position:absolute;left:572px;top:632px;display:flex;gap:12px}
.hero-dots span{width:12px;height:12px;border-radius:50%;background:rgba(255,255,255,.5)}
.hero-dots span:first-child{background:var(--white)}

/* welcome */
.welcome{top:780px;height:540px}
.welcome-text{position:absolute;left:112px;top:64px;width:460px}
.eyebrow{font-family:"Marcellus",Georgia,serif;font-size:22px;letter-spacing:2px;color:var(--navy)}
.welcome h2{font-family:"Marcellus",Georgia,serif;font-weight:400;font-size:46px;color:var(--navy);letter-spacing:2px;margin:4px 0 18px}
.welcome p{font-size:14px;line-height:1.7;color:var(--muted)}
.ticks{list-style:none;margin:20px 0 34px}
.ticks li{display:flex;align-items:center;gap:12px;font-size:14px;color:var(--muted);margin-bottom:14px}
.welcome-art{position:absolute;left:700px;top:90px;width:400px;height:340px;background:radial-gradient(circle at 55% 30%,#e0303d 0 70px,transparent 72px),linear-gradient(180deg,#f4f4f6,#d6d8dc)}

/* services */
.services{top:1320px;height:460px;background:var(--soft);text-align:center}
.section-title{font-family:"Marcellus",Georgia,serif;font-weight:400;font-size:38px;letter-spacing:2px;color:var(--navy)}
.services .section-title{margin-top:44px}
.lead{font-size:14px;color:var(--muted);margin:12px auto 0;width:600px;line-height:1.6}
.service-row{position:absolute;top:176px;left:112px;width:976px;display:flex;justify-content:space-between}
.service{width:290px}
.service-icon{width:104px;height:104px;border-radius:50%;border:3px solid var(--navy);margin:0 auto;display:flex;align-items:center;justify-content:center;background:var(--white)}
.service h3{font-family:"Marcellus",Georgia,serif;font-weight:400;font-size:21px;color:var(--navy);letter-spacing:1px;margin:28px 0 12px}
.service p{font-size:13px;line-height:1.7;color:var(--muted)}
.rule{top:1788px;height:4px;background:var(--navy)}

/* video */
.video{top:1820px;height:500px}
.video-panel{position:absolute;left:600px;top:0;width:600px;height:500px;background:var(--navy)}
.video-copy{position:absolute;left:800px;top:80px;width:320px;color:var(--white)}
.video-copy h2{font-family:"Marcellus",Georgia,serif;font-weight:400;font-size:38px;letter-spacing:2px;margin-bottom:18px}
.video-copy p{font-size:14px;line-height:1.75;color:#cdd3e2;margin-bottom:26px}
.btn-ghost{display:inline-block;border:1px solid var(--white);color:var(--white);font-size:13px;letter-spacing:1px;padding:12px 26px;border-radius:30px}
.video-still{position:absolute;left:112px;top:40px;width:656px;height:420px;background:linear-gradient(135deg,#8a8f96 0%,#5e5a5c 45%,#b1312f 70%,#6d6f75 100%)}
.play{position:absolute;left:288px;top:170px}

/* faq + map */
.faq-map{top:2400px;height:500px}
.faq{position:absolute;left:112px;top:0;width:476px}
.map{position:absolute;left:632px;top:0;width:456px}
.faq .section-title,.map .section-title{text-align:left;margin-bottom:34px}
.faq-item{border:1px solid var(--line);margin-bottom:14px;background:var(--white)}
.faq-q{display:flex;align-items:center;gap:12px;padding:14px 16px;font-size:14px;color:var(--navy);letter-spacing:.5px}
.faq-item.open{background:#f6f7f9}
.faq-item.open .faq-q{border-bottom:1px solid var(--line)}
.faq-a{padding:14px 16px 18px 44px;font-size:13px;line-height:1.7;color:var(--muted)}
.map-canvas{width:456px;height:372px;background:linear-gradient(160deg,#d3dde6 0%,#9fb3c5 40%,#c9b89a 70%,#a7b8c8 100%)}

/* footer */
.site-footer{top:2940px;height:416px;background:var(--footer);color:var(--white)}
.contact{position:absolute;left:112px;top:50px;width:380px}
.site-footer h4{font-family:"Lato",Arial,sans-serif;font-weight:400;font-size:26px;margin-bottom:26px}
.form-row{display:flex;gap:12px;margin-bottom:12px}
.field{flex:1;height:34px;background:var(--white);font-size:12px;color:#777;padding:10px}
.field.msg{height:56px}
.submit{display:inline-block;background:var(--navy);font-size:12px;padding:10px 18px;margin-top:4px}
.address{position:absolute;left:540px;top:50px;width:290px}
.addr-item{display:flex;gap:14px;margin-bottom:20px}
.addr-icon{width:38px;height:38px;border-radius:50%;border:1px solid #888;flex:none;display:flex;align-items:center;justify-content:center}
.addr-item b{display:block;font-size:13px;letter-spacing:1px;margin-bottom:4px}
.addr-item span{font-size:13px;color:#bdbdc2;line-height:1.5}
.footer-brand{position:absolute;left:860px;top:110px}
.footer-brand .brand-dot{background:var(--white)}
.footer-brand .brand{position:static}
.footer-brand .brand-name{color:var(--white)}
.social{display:flex;gap:12px;margin-top:26px}
.social span{width:36px;height:36px;border-radius:50%;border:1px solid #aaa}
.copyright{position:absolute;left:0;top:362px;width:1200px;border-top:1px solid #3b3c3f;padding-top:18px;text-align:center;font-size:13px;color:#9a9aa0}
</style>
</head>
<body>

<header class="site-header">
  <div class="brand"><span class="brand-dot"></span><span class="brand-name">Birchfield Vale Chapter</span></div>
  <nav class="main-nav">
    <a href="#">HOME</a><a href="#">ABOUT US</a><a href="#">SERVICES</a><a href="#">NEWS</a><a href="#">CONTACT US</a>
  </nav>
</header>

<section class="hero" role="img" aria-label="Photo of hands performing CPR on a training mannequin beside an AED unit">
  <div class="hero-panel">
    <h1><span class="l1">BRINGING AEDS</span><span class="l2">IN NEW YORK ONLINE</span></h1>
    <p>Sed ut perspiciatis unde omnis iste natus error sit voluptatem accusantium doloremque laudantium, totam rem.</p>
    <a class="btn" href="#">READ MORE</a>
  </div>
  <div class="hero-dots"><span></span><span></span></div>
</section>

<section class="welcome">
  <div class="welcome-text">
    <div class="eyebrow">WELCOME TO</div>
    <h2>AED DEVICES</h2>
    <p>Sed ut perspiciatis unde omnis iste natus error sit voluptatem accusantium doloremque laudantium, totam rem aperiam, eaque ipsa quae ab illo inventore veritatis et quasi architecto beatae vitae dicta sunt explicabo.</p>
    <ul class="ticks">
      <li><svg width="14" height="14" viewBox="0 0 14 14"><path d="M2 7l3 3 7-7" fill="none" stroke="#0f2352" stroke-width="2"/></svg>Nemo enim ipsam voluptatem quia voluptas sit</li>
      <li><svg width="14" height="14" viewBox="0 0 14 14"><path d="M2 7l3 3 7-7" fill="none" stroke="#0f2352" stroke-width="2"/></svg>Aspernatur aut odit aut fugit, sed quia consequuntur</li>
      <li><svg width="14" height="14" viewBox="0 0 14 14"><path d="M2 7l3 3 7-7" fill="none" stroke="#0f2352" stroke-width="2"/></svg>Magni dolores eos qui ratione voluptatem sequi nesciunt</li>
    </ul>
    <a class="btn" href="#">READ MORE</a>
  </div>
  <div class="welcome-art" role="img" aria-label="Illustration of a red heart above a defibrillator unit with two paddles"></div>
</section>

<section class="services">
  <h2 class="section-title">OUR SERVICES</h2>
  <p class="lead">Sed ut perspiciatis unde omnis iste natus error sit voluptatem accusantium doloremque laudantium</p>
  <div class="service-row">
    <div class="service">
      <div class="service-icon"><svg width="50" height="50" viewBox="0 0 50 50"><rect x="6" y="14" width="38" height="26" rx="4" fill="none" stroke="#0f2352" stroke-width="3"/><path d="M25 20v14M18 27h14" stroke="#0f2352" stroke-width="3"/></svg></div>
      <h3>CUSTOM FIRST AID KITS</h3>
      <p>Sed ut perspiciatis unde omnis iste natus error sit voluptatem accusantium doloremque laudantium, totam rem aperiam, eaque ipsa.</p>
    </div>
    <div class="service">
      <div class="service-icon"><svg width="50" height="50" viewBox="0 0 50 50"><path d="M25 40C10 30 8 22 12 16s11-4 13 1c2-5 9-7 13-1s2 14-13 24z" fill="none" stroke="#0f2352" stroke-width="3"/></svg></div>
      <h3>SERVICING OF KITS</h3>
      <p>Sed ut perspiciatis unde omnis iste natus error sit voluptatem accusantium doloremque laudantium, totam rem aperiam, eaque ipsa.</p>
    </div>
    <div class="service">
      <div class="service-icon"><svg width="50" height="50" viewBox="0 0 50 50"><rect x="10" y="8" width="30" height="34" rx="3" fill="none" stroke="#0f2352" stroke-width="3"/><path d="M17 26h5l3-6 3 10 3-4h3" fill="none" stroke="#0f2352" stroke-width="2.5"/></svg></div>
      <h3>AED DEVICES</h3>
      <p>Sed ut perspiciatis unde omnis iste natus error sit voluptatem accusantium doloremque laudantium, totam rem aperiam, eaque ipsa.</p>
    </div>
  </div>
</section>

<section class="rule"></section>

<section class="video">
  <div class="video-panel"></div>
  <div class="video-still" role="img" aria-label="Video still of a CPR training class kneeling around a mannequin">
    <svg class="play" width="80" height="80" viewBox="0 0 80 80"><circle cx="40" cy="40" r="38" fill="#c8202f" opacity=".9"/><path d="M32 26l22 14-22 14z" fill="#fff"/></svg>
  </div>
  <div class="video-copy">
    <h2>OUR VIDEO</h2>
    <p>Sed ut perspiciatis unde omnis iste natus error sit voluptatem accusantium doloremque laudantium, totam rem aperiam, eaque ipsa quae ab illo inventore veritatis et quasi architecto beatae vitae dicta sunt explicabo. Nemo enim ipsam voluptatem quia voluptas sit aspernatur.</p>
    <span class="btn-ghost">WATCH VIDEO</span>
  </div>
</section>

<section class="faq-map">
  <div class="faq">
    <h2 class="section-title">OUR FAQ'S</h2>
    <div class="faq-item open">
      <div class="faq-q"><svg width="16" height="16" viewBox="0 0 16 16"><circle cx="8" cy="8" r="8" fill="#0f2352"/><path d="M4 8h8" stroke="#fff" stroke-width="2"/></svg>SED UT PERSPICIATIS UNDE OMNIS ISTE?</div>
      <div class="faq-a">Totam rem aperiam eaque ipsa quae ab illo inventore veritatis et quasi architecto beatae vitae dicta sunt explicabo. Nemo enim ipsam voluptatem quia voluptas sit aspernatur aut odit aut fugit, sed quia consequuntur magni dolores.</div>
    </div>
    <div class="faq-item"><div class="faq-q"><svg width="16" height="16" viewBox="0 0 16 16"><circle cx="8" cy="8" r="8" fill="#0f2352"/><path d="M4 8h8M8 4v8" stroke="#fff" stroke-width="2"/></svg>SED UT PERSPICIATIS UNDE OMNIS ISTE?</div></div>
    <div class="faq-item"><div class="faq-q"><svg width="16" height="16" viewBox="0 0 16 16"><circle cx="8" cy="8" r="8" fill="#0f2352"/><path d="M4 8h8M8 4v8" stroke="#fff" stroke-width="2"/></svg>SED UT PERSPICIATIS UNDE OMNIS ISTE?</div></div>
    <div class="faq-item"><div class="faq-q"><svg width="16" height="16" viewBox="0 0 16 16"><circle cx="8" cy="8" r="8" fill="#0f2352"/><path d="M4 8h8M8 4v8" stroke="#fff" stroke-width="2"/></svg>SED UT PERSPICIATIS UNDE OMNIS ISTE?</div></div>
  </div>
  <div class="map">
    <h2 class="section-title">OUR MAP</h2>
    <div class="map-canvas" role="img" aria-label="World map with red location pins marking participating regions"></div>
  </div>
</section>

<footer class="site-footer">
  <div class="contact">
    <h4>Contact Us</h4>
    <div class="form-row"><div class="field">First Name</div><div class="field">Last Name</div></div>
    <div class="form-row"><div class="field">Email</div><div class="field">Phone</div></div>
    <div class="form-row"><div class="field msg">Message</div></div>
    <span class="submit">SUBMIT</span>
  </div>
  <div class="address">
    <h4>Address</h4>
    <div class="addr-item"><span class="addr-icon"><svg width="16" height="16" viewBox="0 0 16 16"><path d="M8 15s5-5 5-9a5 5 0 0 0-10 0c0 4 5 9 5 9z" fill="none" stroke="#fff" stroke-width="1.5"/><circle cx="8" cy="6" r="1.8" fill="#fff"/></svg></span><div><b>ADDRESS</b><span>Main lorem ipsum dummy text<br>lorem ipsum dummy</span></div></div>
    <div class="addr-item"><span class="addr-icon"><svg width="16" height="16" viewBox="0 0 16 16"><path d="M3 2h3l1 3-2 1a8 8 0 0 0 5 5l1-2 3 1v3c-6 1-12-5-11-11z" fill="none" stroke="#fff" stroke-width="1.5"/></svg></span><div><b>PHONE NUMBER</b><span>(555) 014-2290</span></div></div>
    <div class="addr-item"><span class="addr-icon"><svg width="16" height="16" viewBox="0 0 16 16"><rect x="2" y="4" width="12" height="9" fill="none" stroke="#fff" stroke-width="1.5"/><path d="M2 4l6 5 6-5" fill="none" stroke="#fff" stroke-width="1.5"/></svg></span><div><b>EMAIL US</b><span>hello@pulsebeacon-registry.org</span></div></div>
  </div>
  <div class="footer-brand">
    <div class="brand"><span class="brand-dot"></span><span class="brand-name">Birchfield Vale Chapter</span></div>
    <div class="social"><span></span><span></span><span></span><span></span><span></span></div>
  </div>
  <div class="copyright">© Copyright 2019 AED Devices All Rights Reserved.</div>
</footer>

</body>
</html>
```